Post Card Design - Photo on front, details on back. Logo on both sides.

Back: See the photo of my old card. The back worked well, as it gave me lots of space to write on. The address details are still correct, but the logo has changed to Josephine Sans. Logo can be on one line or on two (if two, align it on the left).
Don't include the 'BEAUTIFUL WEDDING DRESSES...' bit.
I'd like to print this on thicker, slightly coarse paper, so don't go too small on detail.
Here are the Trelo paper details: Paper Stock: Natural Uncoated
Paper Thickness: Premium
Finish: None
Front of Card: I'd like to see options for both pictures:
I think the painted image would look best with a frame in a pale shade and the logo in the frame fairly subtle.
The actual dress photo I'd like to see cropped a bit like in my mock up. You'll need to have a look at how the logo would be best placed on this. You can place it anywhere, or add a banner.
See my website for my brand's look: lenaardwyn.co.nz
Target Market(s)
Brides
Industry/Entity Type
Wedding Dresses
Contact Information for Business Card
Front: Photo and logo. Back: with details and lots of empty space. See attached photos for loose brief.
Other font styles liked:
- Josephine Sans
Requirements
Must have
- I hand-write the gown designs and price on the back of the card, so there needs to be plenty of empty space.
Nice to have
- As per brief.
Should not have
- It must look clean, romantic, modern. Timeless.

```html
<!DOCTYPE html>
<html lang="en">
<head>
<meta charset="utf-8">
<title>Lena Ardwyn – Postcard Back</title>
<link rel="stylesheet" href="https://fonts.googleapis.com/css2?family=Josefin+Sans:wght@300&family=Open+Sans:wght@300&display=swap">
<style>
  :root {
    --paper: #ffffff;
    --ink: #111111;
  }
  html, body {
    margin: 0;
    padding: 0;
    overflow: hidden;
    background: var(--paper);
  }
  .postcard-back {
    position: relative;
    width: 1200px;
    height: 800px;
    background: var(--paper);
    color: var(--ink);
    overflow: hidden;
  }
  .brand-name {
    position: absolute;
    left: 86px;
    top: 84px;
    margin: 0;
    font-family: "Josefin Sans", sans-serif;
    font-weight: 300;
    font-size: 57px;
    line-height: 1;
    letter-spacing: 1px;
    text-transform: uppercase;
    white-space: nowrap;
  }
  .contact-list {
    position: absolute;
    left: 747px;
    top: 638px;
    margin: 0;
    padding: 0;
    list-style: none;
    font-family: "Open Sans", sans-serif;
    font-weight: 300;
    font-size: 27px;
    line-height: 40px;
    letter-spacing: -0.5px;
  }
  .contact-item {
    display: flex;
    align-items: center;
    white-space: nowrap;
  }
  .contact-icon {
    width: 22px;
    height: 22px;
    margin-right: 10px;
    flex: none;
    fill: none;
    stroke: var(--ink);
    stroke-width: 1.6;
  }
  .contact-icon--solid {
    fill: var(--ink);
    stroke: none;
  }
</style>
</head>
<body>
  <main class="postcard-back">
    <h1 class="brand-name">Lena Ardwyn</h1>

    <ul class="contact-list">
      <li class="contact-item">
        <svg class="contact-icon contact-icon--solid" viewBox="0 0 24 24" aria-hidden="true">
          <path d="M7.2 3.5c.7-.4 1.4-.2 1.8.5l1.5 2.9c.3.6.2 1.3-.4 1.7l-1.2.8c.6 2.6 2.2 5 4.3 6.5l1.1-.9c.5-.4 1.2-.4 1.7 0l2.5 2c.6.5.6 1.3.1 1.9l-1.2 1.3c-.7.7-1.8 1-2.8.6-5-2-8.6-6.8-9.1-12.2-.1-1 .4-2 1.2-2.6z"/>
        </svg>
        <span class="contact-text">0204 555 0187</span>
      </li>
      <li class="contact-item">
        <svg class="contact-icon" viewBox="0 0 24 24" aria-hidden="true">
          <rect x="3" y="6" width="18" height="12"/>
          <path d="M3 6l9 7 9-7M3 18l7-6M21 18l-7-6"/>
        </svg>
        <span class="contact-text">lena@lenaardwyn.co.nz</span>
      </li>
      <li class="contact-item">
        <svg class="contact-icon" viewBox="0 0 24 24" aria-hidden="true">
          <circle cx="12" cy="12" r="9"/>
          <ellipse cx="12" cy="12" rx="4" ry="9"/>
          <path d="M3 12h18M4.5 7.5h15M4.5 16.5h15"/>
        </svg>
        <span class="contact-text">lenaardwyn.co.nz</span>
      </li>
    </ul>
  </main>
</body>
</html>
```